Business Card Design

New business card design

Target Market(s)

Residential & Commercial Property Managers

Industry/Entity Type

Plumbing Services

Contact Information for Business Card

Name - Rowan Keddle, title - Director, Phone Number - 0431 286 517, email - rowan@tbk-plumbing.com.au, Company ABN - 73 215 904 386,

Font styles to use
Sans Serif

Colors
0054AA
0677BA
7BADD7
CADEEF
E8F1F8

```html
<!DOCTYPE html>
<html lang="en">
<head>
<meta charset="utf-8">
<title>TBK Plumbing Services – Business Cards</title>
<link rel="stylesheet" href="https://fonts.googleapis.com/css2?family=Roboto:wght@300;400;700&display=swap">
<style>
  :root {
    --backdrop: #2b2b2c;
    --card-black: #1c1d1f;
    --card-white: #f6f6f4;
    --band-taupe: #7b7068;
    --blue-deep: #0054AA;
    --blue-mid: #0677BA;
    --blue-sky: #7BADD7;
    --blue-pale: #CADEEF;
    --blue-mist: #E8F1F8;
    --ink-dark: #1e1e20;
    --ink-grey: #77736f;
    --ink-white: #ffffff;
    --ink-soft: #ece8e4;
  }
  * { box-sizing: border-box; margin: 0; padding: 0; }
  html, body {
    width: 1200px; height: 852px; overflow: hidden;
    background: var(--backdrop);
    font-family: "Roboto", sans-serif;
  }
  .stage {
    position: relative; width: 1200px; height: 852px;
    display: flex; align-items: center; justify-content: center; gap: 60px;
  }
  .card {
    position: relative; width: 520px; height: 297px;
    border-radius: 18px; overflow: hidden;
    box-shadow: 0 4px 0 var(--blue-mid), 0 14px 30px rgba(0,0,0,.45);
  }

  /* Wordmark */
  .wordmark__name {
    font-weight: 300; font-size: 64px; letter-spacing: 6px; line-height: 1;
    color: var(--ink-white);
  }
  .wordmark__tag {
    display: block; margin-top: 8px;
    font-weight: 300; font-size: 13px; letter-spacing: 6px;
    color: var(--ink-grey);
  }

  /* Back side */
  .card--back { background: var(--card-black); }
  .card--back .wordmark {
    position: absolute; left: 0; right: 0; top: 108px; text-align: center;
  }

  /* Front side */
  .card--front { background: var(--card-white); }
  .card--front .wordmark { position: absolute; left: 26px; top: 22px; }
  .card--front .wordmark__name { color: var(--ink-dark); font-size: 48px; }
  .card--front .wordmark__tag { font-size: 11px; letter-spacing: 5px; margin-top: 6px; }

  .band {
    position: absolute; left: 0; right: 0; top: 108px; height: 138px;
    background: var(--band-taupe);
  }
  .band__step {
    position: absolute; right: 0; top: 70px; width: 90px; height: 176px;
    background: var(--band-taupe);
  }
  .accent-disc {
    position: absolute; right: 38px; top: 60px; width: 150px; height: 150px;
    border-radius: 50%; background: var(--blue-mid);
    box-shadow: 0 0 0 8px var(--card-white);
  }

  .contact {
    position: absolute; left: 26px; top: 116px; color: var(--ink-white);
  }
  .contact__name { font-weight: 700; font-size: 18px; line-height: 22px; }
  .contact__title { font-weight: 300; font-size: 12px; line-height: 15px; color: var(--blue-pale); margin-bottom: 6px; }
  .contact__list { list-style: none; }
  .contact__item {
    display: flex; align-items: center; gap: 8px;
    font-weight: 300; font-size: 12px; line-height: 18px; color: var(--ink-soft);
  }
  .contact__item svg { width: 11px; height: 11px; fill: var(--blue-mist); flex: none; }
  .contact__label { font-weight: 400; color: var(--blue-pale); }
  .address {
    position: absolute; left: 26px; bottom: 20px;
    font-size: 12px; font-weight: 400; color: var(--ink-dark);
  }
</style>
</head>
<body>
<main class="stage">
  <section class="card card--back" aria-label="Card back">
    <div class="wordmark">
      <div class="wordmark__name">TBK</div>
      <span class="wordmark__tag">plumbing services</span>
    </div>
  </section>

  <section class="card card--front" aria-label="Card front">
    <div class="wordmark">
      <div class="wordmark__name">TBK</div>
      <span class="wordmark__tag">plumbing services</span>
    </div>
    <div class="band"></div>
    <div class="band__step"></div>
    <div class="accent-disc" aria-hidden="true"></div>
    <div class="contact">
      <p class="contact__name">Rowan Keddle</p>
      <p class="contact__title">Director</p>
      <ul class="contact__list">
        <li class="contact__item">
          <svg viewBox="0 0 12 12" aria-hidden="true"><path d="M3 1l2 2.5-1.2 1.2a7 7 0 0 0 3.5 3.5L8.5 7 11 9l-1.3 2C5 11 1 7 1 2.3z"/></svg>
          0431 286 517
        </li>
        <li class="contact__item">
          <svg viewBox="0 0 12 12" aria-hidden="true"><path d="M1 2.5h10v7H1z M1.6 3l4.4 3.4L10.4 3" stroke="#7b7068" stroke-width=".9"/></svg>
          rowan@tbk-plumbing.com.au
        </li>
        <li class="contact__item">
          <svg viewBox="0 0 12 12" aria-hidden="true"><circle cx="6" cy="6" r="5"/><path d="M1 6h10M6 1c-2.5 3-2.5 7 0 10M6 1c2.5 3 2.5 7 0 10" stroke="#7b7068" stroke-width=".8" fill="none"/></svg>
          www.tbk-plumbing.com.au
        </li>
        <li class="contact__item">
          <svg viewBox="0 0 12 12" aria-hidden="true"><rect x="1" y="2" width="10" height="8" rx="1"/></svg>
          <span><span class="contact__label">ABN</span> 73 215 904 386</span>
        </li>
      </ul>
    </div>
    <p class="address">12 Harbour Rd, Brookvale NSW 2100</p>
  </section>
</main>
</body>
</html>
```